Mortgage Company ready to make a statement!

We have a basic logo that I am fairly happy with ... but it could use a little bit of tweaking before we order the sign for our building. We also want some knock-your-socks-off business cards.
Problem: Inside of our Mortgage Office (Bright Fern Mortgage Group), we are going to have a coffee lounge (Sunbrew Cafe) for Realtors to use instead of the local Cuppington to meet with homebuyers. The office and coffee lounge are in an industrial building and is decorated with cozy overstuffed chairs, a hodge podge of interesting lamps and furniture, and goal is to make it as inviting as possible. However, we are a financial institution... so we need to keep it pretty clean as well.
One of my favorite marketing ideas is to cut a house key for everyone who buys a home using us with a key that matches our logo. There's only one key shape that works really well, so that needs to match the logo in order for the idea to work. I'll attach an image of the key blank.... although the way the key hole cut out looks terrible, so I was thinking of having them just do a thin outline instead.
Would like a similar, matching logo for the Sunbrew Cafe... but possibly something that would be a little less formal and would be cute on a coffee mug- nothing stuffy.
AND, we're opening a home inspection company as well, and we would like that logo and branding to match. The home inspection company is "Bright Fern Home Inspections"
We were thinking that for the home inspection company , we could use a magnifying glass shape inside of the house shape for the logo, use a keyhole shape inside of the same house for the mortgage company, and use a coffee cup inside of the house shape for Sunbrew Cafe.
Just getting stuck and need to help. I designed the attached logo myself, and that is what we are currently using. Designers at local printing companies have failed to impress us.
The mortgage industry has a lot of numbers and logos, etc that they require us to put on our business cards... so it's hard to keep them looking clean.
HELP! HELP! :)

```html
<!DOCTYPE html>
<html lang="en">
<head>
<meta charset="utf-8">
<title>Bright Fern Mortgage Group – Business Card</title>
<link href="https://fonts.googleapis.com/css2?family=Marcellus&family=Marcellus+SC&family=Open+Sans:wght@400;600&display=swap" rel="stylesheet">
<style>
  :root {
    --backdrop: #9e9e9e;
    --paper: #ffffff;
    --brand-blue: #25688a;
    --brand-blue-deep: #21617f;
    --slate: #545566;
    --ink: #2b2b33;
  }
  html, body {
    margin: 0;
    padding: 0;
    width: 1200px;
    height: 900px;
    overflow: hidden;
    background: var(--backdrop);
  }
  .canvas {
    position: relative;
    width: 1200px;
    height: 900px;
  }
  .card {
    position: absolute;
    top: 306px;
    height: 271px;
    overflow: hidden;
  }
  /* Front */
  .card-front {
    left: 149px;
    width: 439px;
    background: var(--paper);
  }
  .name-tab {
    position: absolute;
    left: 0;
    top: 26px;
  }
  .holder {
    position: absolute;
    left: 34px;
    top: 27px;
  }
  .holder-name {
    margin: 0;
    font-family: "Marcellus SC", "Marcellus", serif;
    font-size: 15px;
    letter-spacing: 0.3px;
    color: var(--brand-blue);
    line-height: 18px;
  }
  .holder-role {
    margin: 0;
    font-family: "Open Sans", sans-serif;
    font-size: 12px;
    color: var(--ink);
    line-height: 16px;
  }
  .wordmark {
    position: absolute;
    right: 24px;
    top: 96px;
    text-align: right;
    font-family: "Marcellus", serif;
    font-weight: 400;
    color: var(--brand-blue);
    line-height: 1;
  }
  .wordmark-main {
    display: block;
    font-size: 36px;
    letter-spacing: 0.5px;
  }
  .wordmark-sub {
    display: block;
    margin-top: 6px;
    font-size: 20px;
  }
  .contact-list {
    position: absolute;
    left: 26px;
    top: 189px;
    margin: 0;
    padding: 0;
    list-style: none;
    font-family: "Open Sans", sans-serif;
    font-size: 12px;
    color: var(--ink);
  }
  .contact-list li {
    display: flex;
    align-items: center;
    height: 16px;
  }
  .contact-list svg {
    width: 9px;
    height: 9px;
    margin-right: 6px;
    fill: var(--brand-blue);
  }
  .address {
    position: absolute;
    right: 21px;
    top: 204px;
    margin: 0;
    text-align: right;
    font-family: "Open Sans", sans-serif;
    font-style: normal;
    font-size: 12px;
    line-height: 16px;
    color: var(--ink);
  }
  .footer-bands {
    position: absolute;
    left: 0;
    bottom: 0;
  }
  /* Back */
  .card-back {
    left: 608px;
    width: 441px;
    height: 272px;
    background: var(--brand-blue);
  }
  .pattern-field {
    position: absolute;
    inset: 0;
    background: linear-gradient(180deg, var(--brand-blue) 0%, var(--brand-blue-deep) 100%);
  }
  .back-wordmark {
    position: absolute;
    left: 0;
    right: 0;
    top: 98px;
    text-align: center;
    font-family: "Marcellus", serif;
    color: var(--paper);
    line-height: 1;
  }
  .back-wordmark .wordmark-main {
    font-size: 42px;
  }
  .back-wordmark .wordmark-sub {
    margin-top: 6px;
    font-size: 24px;
  }
  .back-web {
    position: absolute;
    left: 0;
    right: 0;
    top: 229px;
    margin: 0;
    text-align: center;
    font-family: "Open Sans", sans-serif;
    font-size: 12px;
    color: var(--paper);
  }
</style>
</head>
<body>
<main class="canvas">
  <section class="card card-front" aria-label="Business card front">
    <svg class="name-tab" width="30" height="37" viewBox="0 0 30 37" aria-hidden="true">
      <polygon points="0,0 11,0 16,37 0,37" fill="var(--slate)"/>
      <polygon points="11,0 28,0 28,37 16,37" fill="var(--brand-blue)"/>
    </svg>
    <div class="holder">
      <p class="holder-name">DANIEL HARPER</p>
      <p class="holder-role">Managing Director</p>
    </div>

    <div class="wordmark">
      <span class="wordmark-main">BRIGHT FERN</span>
      <span class="wordmark-sub">Mortgage Group</span>
    </div>

    <ul class="contact-list">
      <li>
        <svg viewBox="0 0 10 10" aria-hidden="true"><path d="M2 0.5 L3.6 2.6 L2.7 3.6 Q3.8 5.9 6.3 7.3 L7.4 6.4 L9.5 8 L8.4 9.5 Q3.5 8.8 0.5 1.6 Z"/></svg>
        (044)555018246
      </li>
      <li>
        <svg viewBox="0 0 10 10" aria-hidden="true"><rect x="0.5" y="2" width="9" height="6.5"/><polyline points="0.5,2 5,5.6 9.5,2" fill="none" stroke="#fff" stroke-width="1"/></svg>
        hello@brightfern.com
      </li>
      <li>
        <svg viewBox="0 0 10 10" aria-hidden="true"><circle cx="5" cy="5" r="4.5"/><path d="M0.5 5 H9.5 M5 0.5 Q2.5 5 5 9.5 M5 0.5 Q7.5 5 5 9.5" stroke="#fff" stroke-width="0.8" fill="none"/></svg>
        www.brightfernloans.com
      </li>
    </ul>

    <address class="address">88, Maple Row Street,<br>Fernvale, FV 12345</address>

    <svg class="footer-bands" width="439" height="19" viewBox="0 0 439 19" aria-hidden="true">
      <polygon points="0,5 217,5 209,19 0,19" fill="var(--slate)"/>
      <polygon points="223,0 439,0 439,19 208,19" fill="var(--brand-blue)"/>
    </svg>
  </section>

  <section class="card card-back" aria-label="Business card back">
    <div class="pattern-field" role="img" aria-label="Faint repeating brand pattern across the card back"></div>
    <div class="back-wordmark">
      <span class="wordmark-main">BRIGHT FERN</span>
      <span class="wordmark-sub">Mortgage Group</span>
    </div>
    <p class="back-web">www.brightfern.com</p>
  </section>
</main>
</body>
</html>
```